Velmora Freightway Solutions Business cards

Would like a very unique design catchy but professional for business cards. Please use log provided.Marlon WellsCeo and Founder TransCon Logistix Solutions1-888-913-3225mwells@tlsolutionsus.comwww.tlsolutionsus.com

```html
<!DOCTYPE html>
<html lang="en">
<head>
<meta charset="utf-8">
<title>Velmora Freightway Solutions – Business Cards</title>
<link rel="stylesheet" href="https://fonts.googleapis.com/css2?family=Open+Sans:wght@400;600;700&display=swap">
<style>
  :root {
    --brand-blue: #1574bf;
    --brand-red: #e3242b;
    --ink: #2b2b2b;
    --divider: #c9ccd1;
    --card-white: #ffffff;
    --backdrop: #1d1e20;
  }
  * { box-sizing: border-box; margin: 0; padding: 0; }
  html, body {
    width: 1200px; height: 960px; overflow: hidden;
    background: var(--backdrop);
    font-family: "Open Sans", Arial, sans-serif;
  }
  .stage {
    position: relative; width: 1200px; height: 960px;
  }
  .card {
    position: absolute; width: 588px; height: 336px;
    overflow: hidden; border-radius: 3px;
    box-shadow: 0 18px 40px rgba(0,0,0,.55);
  }
  /* Back of card */
  .card-back {
    left: 420px; top: 110px;
    background: var(--brand-blue);
    color: var(--card-white);
    display: flex; flex-direction: column; align-items: center; justify-content: center;
    gap: 26px;
  }
  .card-back .brand-name {
    font-weight: 700; font-size: 40px; line-height: 1.1; text-align: center;
    letter-spacing: .5px;
  }
  .card-back .web {
    font-weight: 600; font-size: 16px; letter-spacing: 2px;
  }
  /* Front of card */
  .card-front {
    left: 190px; top: 500px;
    background: var(--card-white);
  }
  .band-top {
    position: absolute; right: 0; top: 0; width: 46%; height: 9px;
    background: var(--brand-blue);
  }
  .band-bottom {
    position: absolute; left: 0; bottom: 0; width: 48%; height: 9px;
    background: var(--brand-blue);
  }
  .brand-block {
    position: absolute; left: 26px; top: 96px; width: 230px;
    display: flex; align-items: center; gap: 10px;
  }
  .brand-block .mark {
    width: 16px; height: 16px; background: var(--brand-red); flex: none;
  }
  .brand-block .brand-name {
    color: var(--brand-blue); font-weight: 700; font-size: 22px; line-height: 1.15;
  }
  .divider {
    position: absolute; left: 286px; top: 60px; width: 1px; height: 200px;
    background: var(--divider);
  }
  .contact {
    position: absolute; left: 304px; top: 66px; color: var(--ink);
  }
  .contact .person {
    color: var(--brand-blue); font-weight: 700; font-size: 19px; text-transform: uppercase;
  }
  .contact .role {
    color: var(--brand-red); font-weight: 600; font-size: 14px; text-transform: uppercase;
    margin-bottom: 10px;
  }
  .contact .address { font-size: 14px; line-height: 1.35; margin-bottom: 8px; }
  .contact ul { list-style: none; font-size: 14px; }
  .contact li { display: flex; align-items: center; gap: 8px; line-height: 1.6; }
  .contact li svg { width: 12px; height: 12px; flex: none; }
</style>
</head>
<body>
<main class="stage">
  <section class="card card-back" aria-label="Card back">
    <p class="brand-name">Velmora Freightway<br>Solutions</p>
    <p class="web">www.vfwayroutes.com</p>
  </section>

  <section class="card card-front" aria-label="Card front">
    <div class="band-top"></div>
    <div class="band-bottom"></div>

    <div class="brand-block">
      <span class="mark"></span>
      <p class="brand-name">Velmora Freightway Solutions</p>
    </div>

    <div class="divider"></div>

    <div class="contact">
      <p class="person">Dorian Pike</p>
      <p class="role">CEO and Founder</p>
      <p class="address">2750 Lindell Park Rd<br>Atlanta, GA 30341</p>
      <ul>
        <li>
          <svg viewBox="0 0 12 12"><circle cx="6" cy="6" r="5.5" fill="none" stroke="#1574bf"/><path d="M4 3.2l1 1.6-.7.7c.4.9 1 1.5 1.9 1.9l.7-.7 1.6 1-.6 1.1C5.6 8.7 3.3 6.4 3 4z" fill="#1574bf"/></svg>
          1-888-470-6158
        </li>
        <li>
          <svg viewBox="0 0 12 12"><rect x="1" y="3" width="10" height="7" fill="#1574bf"/><path d="M1 3l5 4 5-4" fill="none" stroke="#fff" stroke-width="1"/></svg>
          dpike@vfwayroutes.com
        </li>
        <li>
          <svg viewBox="0 0 12 12"><circle cx="6" cy="6" r="5" fill="none" stroke="#1574bf" stroke-width="1.2"/><path d="M1 6h10M6 1c-2 2.6-2 7.4 0 10M6 1c2 2.6 2 7.4 0 10" fill="none" stroke="#1574bf" stroke-width=".9"/></svg>
          www.vfwayroutes.com
        </li>
      </ul>
    </div>
  </section>
</main>
</body>
</html>
```